Local Chiropractor Needs Up Scale Webdesign

This website needs to have an upscale look with a very modern feel. Below is the information and websites to reference

Add Logo that is attached

Build a color scheme similar to this website image titled "chiro-1"

Must Include these pages in a horizontal menu bar in this order:
Home, Meet Our Staff, Patient Testimonials, Videos, Work Place Wellness, Contact

Build a "classy looking" Make An Appointment Button into the header with the contact info below

Phone Number:
555-314-2719

Address:
3168 Pelham Orchard Lane, #240
Brookhaven, MN 55390

This website needs 4 rotating banners. Please reference a layout similar to this for the banners: http://drmorlatz.example/. However design it nicer than this website, this website is very boring and doesn't flow with the colors properly

Below are the description for each banner

Rotating Banner #1
Use Image: Pediatrics
Two lines of text. First line title line, second description. Use Latin text for fill

Rotating Banner #2
Use Image: Aging Gracefully

Rotating Banner #3
Use Image: Pregnancy

Rotating Banner #4
Use Image: Athletics

I'd like to see a free consultation box similar to the "chiro-1" image. Fields to include are: First Name, Last Name, Phone Number, Comments.

For the body, please fill it with latin text. Please design a professional body layout. You can include a box in the right column for the hours

Office Hours
Monday: 8:00-11:00, 2:00-5:00
Tuesday: 8:30-11:00, 2:00-5:30
Wednesday: 8:00-11:00, 2:00-5:00
Thursday: 10:00-12:00, 2:30-5:00
Friday: 8:00-10:00, 1:00-5:00
Saturday: Closed
Sunday: Closed

For the footer please design something similar to the: http://drmorlatz.example/

Also include in the Footer: Powered by Brightline Site Works

```html
<!DOCTYPE html>
<html lang="en">
<head>
<meta charset="utf-8">
<title>Evergreen Path Chiropractic – Home</title>
<link rel="stylesheet" href="https://fonts.googleapis.com/css2?family=Open+Sans:ital,wght@0,400;0,600;0,700;1,400&family=Oswald:wght@300;400&display=swap">
<style>
:root{
  --charcoal:#464646;
  --charcoal-dark:#3a3a3a;
  --lime:#c8dc32;
  --olive:#8a9b1f;
  --leaf:#8cc63f;
  --ink:#333;
  --orange:#d24a1e;
  --cyan:#22c3cc;
  --night:#111;
  --white:#fff;
}
*{box-sizing:border-box;margin:0;padding:0}
html,body{width:823px;height:1200px;overflow:hidden;background:var(--white)}
body{position:relative;font-family:'Open Sans',sans-serif;color:var(--ink)}
a{color:inherit;text-decoration:none}
.abs{position:absolute}
.cond{font-family:'Oswald',sans-serif;font-weight:300}

/* header */
.site-header{left:0;top:0;width:823px;height:72px;background:var(--charcoal)}
.header-contact{left:86px;top:16px;color:var(--white);font-size:10px;line-height:13px}
.header-contact .row{display:flex;gap:6px;align-items:flex-start;margin-bottom:4px}
.brand{left:332px;top:22px;display:flex;align-items:center;gap:8px;color:var(--leaf);font-weight:600;font-size:18px}
.brand-dot{width:20px;height:20px;border-radius:50%;background:var(--leaf)}
.appointment-btn{left:622px;top:15px;width:116px;height:42px;background:var(--lime);border:2px solid #b0c226;box-shadow:inset 0 0 0 2px var(--lime),inset 0 0 0 3px #a6b722;text-align:center;color:#4a4a1a;font-family:'Oswald',sans-serif;font-size:11px;line-height:13px;padding-top:3px}
.appointment-btn svg{display:block;margin:0 auto 2px}

/* navigation */
.main-nav{left:0;top:72px;width:823px;height:31px;background:var(--lime)}
.main-nav ul{list-style:none;display:flex;position:absolute;left:85px;top:0;height:31px;border-left:1px solid #b3c52a}
.main-nav li{height:31px;line-height:31px;text-align:center;font-family:'Oswald',sans-serif;font-weight:300;font-size:11px;color:#333;border-right:1px solid #b3c52a}

/* hero */
.hero-image{left:0;top:103px;width:823px;height:355px;background:linear-gradient(100deg,#5b4a2a 0%,#7c8a3d 25%,#a9b765 45%,#6e7c3a 70%,#4a3d22 100%)}
.hero-caption{left:68px;top:236px;width:445px;height:112px;background:rgba(200,220,50,.78);padding:6px 18px}
.hero-caption h1{font-size:23px;font-weight:700;color:#3a3a3a;line-height:32px;white-space:nowrap;letter-spacing:-.2px}
.hero-caption p{font-size:10.5px;line-height:14px;color:#444;margin-top:2px;width:352px}
.know-more{display:inline-block;margin-top:8px;background:var(--charcoal);color:var(--white);font-size:11px;padding:4px 9px}
.slider-arrow{top:270px;width:22px;height:22px;background:var(--charcoal-dark);color:var(--white);font-size:13px;text-align:center;line-height:20px}

/* welcome */
.welcome{left:87px;top:472px;width:440px}
.welcome h2{font-size:18px;font-weight:600;color:var(--leaf)}
.welcome p{font-size:9.2px;line-height:14.5px;color:#444;margin-top:1px;width:356px}

.video-card{left:85px;top:551px;width:262px;height:166px;background:#e4eaf0}
.video-bar{height:22px;background:rgba(60,60,60,.9);color:var(--white);font-size:11px;line-height:22px;padding-left:5px;position:relative}
.video-bar svg{position:absolute;right:8px;top:6px}
.video-still{position:absolute;left:0;top:22px;width:262px;height:144px;background:linear-gradient(160deg,#d7dfe6,#f4f6f8 60%,#c9d2da)}
.play-btn{position:absolute;left:117px;top:49px;width:44px;height:30px;border-radius:7px;background:var(--charcoal)}

.team-card{left:85px;top:726px;width:262px;height:99px;background:var(--charcoal)}
.team-card h3{text-align:center;color:var(--white);font-size:12px;font-weight:600;margin-top:4px}
.team-photo{top:26px;width:74px;height:58px}
.team-photo .label{position:absolute;left:0;right:0;top:28px;text-align:center;font-size:9px;line-height:11px;color:#3a3a3a;font-weight:600}
.team-photo .label span{font-weight:400;display:block}

.service{left:367px;width:148px}
.service h4{display:flex;align-items:center;gap:6px;font-size:14.5px;font-weight:400;color:#444}
.service p{font-size:8.6px;line-height:10.6px;color:#555;text-align:justify;hyphens:auto}

.testimonial{left:85px;top:848px;width:429px;height:107px;background:var(--charcoal);color:var(--white);text-align:center}
.testimonial h3{font-size:12.5px;font-weight:600;margin-top:5px}
.testimonial blockquote{font-style:italic;font-size:9.8px;line-height:15.5px;margin:8px 8px 0;padding:0 4px}
.testimonial cite{position:absolute;left:362px;top:70px;color:var(--lime);font-size:10px;line-height:13px;font-style:italic;text-align:center}
.dots{position:absolute;left:197px;top:94px;display:flex;gap:3px}
.dots i{width:6px;height:6px;border-radius:50%;background:var(--white)}

/* consultation form */
.consult{left:532px;top:483px;width:206px;height:227px;background:var(--lime);box-shadow:0 6px 8px -4px rgba(0,0,0,.35)}
.consult-top{position:absolute;left:0;top:0;width:206px;height:58px}
.consult-text{position:absolute;left:0;top:0;width:206px;text-align:center}
.consult-text .lead{color:var(--lime);font-family:'Oswald',sans-serif;font-weight:300;font-size:11px;margin-top:2px}
.consult-text .big{color:var(--white);font-family:'Oswald',sans-serif;font-size:13.5px;letter-spacing:1.3px;margin-top:1px}
.consult-text .today{color:var(--lime);font-family:'Oswald',sans-serif;font-weight:300;font-size:11px}
.consult h5{position:absolute;top:66px;width:206px;text-align:center;font-family:'Oswald',sans-serif;font-weight:400;font-size:11px;color:#333}
.field{position:absolute;left:23px;width:160px;height:17px;background:var(--white);font-size:7.5px;color:#777;padding:4px 6px;font-family:'Oswald',sans-serif;font-weight:300}
.submit{position:absolute;left:23px;top:197px;width:160px;height:17px;background:var(--olive);color:var(--white);font-size:9px;font-weight:600;letter-spacing:1px;text-align:center;line-height:17px}

/* office hours box */
.hours{left:532px;top:747px;width:206px;height:206px;background:var(--charcoal);box-shadow:0 3px 4px rgba(0,0,0,.25)}
.hours h3{text-align:center;color:var(--white);font-family:'Oswald',sans-serif;font-weight:300;font-size:14px;margin-top:3px}
.hours table{position:absolute;left:5px;top:24px;width:196px;height:177px;background:var(--lime);border-collapse:collapse;font-size:9.8px;color:#333}
.hours td{border-bottom:1px solid #b6c92a;padding-left:7px}
.hours tr:last-child td{border-bottom:none}
.hours td.day{width:64px}

/* footer */
.site-footer{left:0;top:970px;width:823px;height:230px;background:var(--night);color:var(--white)}
.tab{top:0;height:36px;line-height:36px;text-align:center;font-size:18px}
.tab-info{left:85px;width:326px;background:var(--orange)}
.tab-news{left:413px;width:325px;background:var(--cyan)}
.footer-heading{font-family:'Oswald',sans-serif;font-weight:300;font-size:13px;border-bottom:1px solid var(--white);display:inline-block;line-height:16px}
.footer-contact{left:87px;top:47px;font-family:'Oswald',sans-serif;font-weight:300;font-size:10px;color:var(--white)}
.footer-contact .row{display:flex;gap:8px;align-items:center;margin-top:12px;line-height:15px}
.footer-contact .row span{color:var(--white)}
.map{left:284px;top:62px;width:187px;height:109px;background:linear-gradient(135deg,#d9e4cf,#c6d7bd 50%,#b9cfe0);border:2px solid var(--lime)}
.footer-hours{left:513px;top:46px;width:142px;font-family:'Oswald',sans-serif;font-weight:300}
.footer-hours ul{list-style:none;margin-top:8px}
.footer-hours li{display:flex;font-size:8.5px;height:17.7px;line-height:16px;border-bottom:1px solid #888}
.footer-hours li:last-child{border-bottom:none}
.footer-hours li b{font-weight:300;width:60px}
</style>
</head>
<body>

<header class="site-header abs">
  <div class="header-contact abs">
    <div class="row">
      <svg width="9" height="13" viewBox="0 0 9 13"><path d="M4.5 0A4.5 4.5 0 0 0 0 4.5C0 8 4.5 13 4.5 13S9 8 9 4.5A4.5 4.5 0 0 0 4.5 0z" fill="#fff"/><circle cx="4.5" cy="4.5" r="1.7" fill="#464646"/></svg>
      <span>3168 Pelham Orchard Lane, #240<br>Brookhaven, MN 55390</span>
    </div>
    <div class="row">
      <svg width="11" height="11" viewBox="0 0 11 11"><circle cx="5.5" cy="5.5" r="4.8" fill="none" stroke="#fff"/><path d="M3.5 3c.4 2 1.6 3.8 4 4.6l.6-.9-1-.6-.5.5C5.6 6.2 4.9 5.4 4.5 4.4l.5-.5-.6-1z" fill="#fff"/></svg>
      <span>555-314-2719</span>
    </div>
  </div>
  <div class="brand abs"><span class="brand-dot"></span>Evergreen Path</div>
  <a class="appointment-btn abs">
    <svg width="18" height="17" viewBox="0 0 18 17"><rect x="1" y="2" width="16" height="14" rx="2" fill="none" stroke="#333" stroke-width="1.4"/><line x1="1" y1="5.5" x2="17" y2="5.5" stroke="#333" stroke-width="1.4"/><path d="M5.5 10.5l2.5 2.5 4.5-5" fill="none" stroke="#333" stroke-width="1.6"/></svg>
    Make An Appointment
  </a>
</header>

<nav class="main-nav abs">
  <ul>
    <li style="width:78px">Home</li>
    <li style="width:117px">Meet Our Staff</li>
    <li style="width:139px">Patient Testimonials</li>
    <li style="width:84px">Videos</li>
    <li style="width:142px">Work Place Wellness</li>
    <li style="width:93px">Contact</li>
  </ul>
</nav>

<section class="hero-image abs" role="img" aria-label="Two smiling women jogging together on a forest trail, holding water bottles"></section>
<div class="hero-caption abs">
  <h1>The standard Lorem Ipsum passage</h1>
  <p>Sed ut perspiciatis unde omnis iste natus error sit voluptatem accusantium doloremque laudantium, totam rem tore veritatis</p>
  <a class="know-more">Know More</a>
</div>
<div class="slider-arrow abs" style="left:0">&laquo;</div>
<div class="slider-arrow abs" style="left:801px">&raquo;</div>

<section class="welcome abs">
  <h2>Welcome To Evergreen Path</h2>
  <p>There are many variations of passages of Lorem Ipsum available, but the majority have suffered alteration in some form, by injected humour, or randomised words which don't look even slightly believable. If you</p>
</section>

<div class="video-card abs">
  <div class="video-bar">Lorem Ipsum is simply dummy text
    <svg width="10" height="10" viewBox="0 0 10 10"><circle cx="2" cy="5" r="1.6" fill="#fff"/><circle cx="8" cy="2" r="1.6" fill="#fff"/><circle cx="8" cy="8" r="1.6" fill="#fff"/><path d="M2 5L8 2M2 5l6 3" stroke="#fff"/></svg>
  </div>
  <div class="video-still" role="img" aria-label="Video still of two skiers racing down a snowy slope">
    <div class="play-btn"><svg width="44" height="30" viewBox="0 0 44 30"><path d="M18 9l10 6-10 6z" fill="#fff"/></svg></div>
  </div>
</div>

<div class="team-card abs">
  <h3>Our Team</h3>
  <div class="team-photo abs" style="left:9px;background:linear-gradient(#d9d67a,#b9b64a)" role="img" aria-label="Portrait of the practice manager">
    <div class="label">laura benson<span>Manager</span></div>
  </div>
  <div class="team-photo abs" style="left:94px;background:linear-gradient(#c9a58c,#6b4f3e)" role="img" aria-label="Portrait of a team member"></div>
  <div class="team-photo abs" style="left:178px;background:linear-gradient(#8a8a8a,#3a3a3a)" role="img" aria-label="Portrait of a team member"></div>
</div>

<div class="service abs" style="top:549px">
  <h4><svg width="28" height="26" viewBox="0 0 28 26"><circle cx="14" cy="13" r="11" fill="var(--lime)"/></svg>Pediatrics</h4>
  <p>There are many variations of passages of Lorem Ipsum available, but the majority have suffered</p>
</div>
<div class="service abs" style="top:612px">
  <h4><svg width="20" height="30" viewBox="0 0 20 30"><circle cx="10" cy="5" r="4" fill="var(--lime)"/><path d="M5 11h10l2 17H3z" fill="var(--lime)"/></svg>Aging Gracefully</h4>
  <p>There are many variations of passages of Lorem Ipsum available, but the majority have suffered</p>
</div>
<div class="service abs" style="top:683px">
  <h4><svg width="20" height="32" viewBox="0 0 20 32"><circle cx="9" cy="5" r="4" fill="var(--lime)"/><path d="M6 11h6c4 3 4 9 0 11v9H6z" fill="var(--lime)"/></svg>Pregnancy</h4>
  <p>There are many variations of passages of Lorem Ipsum available, but the majority have suffered</p>
</div>
<div class="service abs" style="top:757px">
  <h4><svg width="30" height="26" viewBox="0 0 30 26"><circle cx="22" cy="5" r="4" fill="var(--lime)"/><path d="M8 10l10-1 3 7 6 2M16 12l-4 8-8 3M18 16l-2 8" fill="none" stroke="var(--lime)" stroke-width="3" stroke-linecap="round"/></svg>Athletics</h4>
  <p>There are many variations of passages of Lorem Ipsum available, but the majority have suffered</p>
</div>

<section class="testimonial abs">
  <h3>Testrimonial</h3>
  <blockquote><b style="font-size:15px;font-style:normal">&ldquo;</b> There are many variations of passages of Lorem Ipsum available, but the majority have suffered alteration in some form, by injected humour, or randomised words which don't look even slightly believable <b style="font-size:15px;font-style:normal">&rdquo;</b></blockquote>
  <cite>maria holt<br>USA</cite>
  <div class="dots"><i></i><i></i><i></i><i></i></div>
</section>

<aside class="consult abs">
  <svg class="consult-top" viewBox="0 0 206 58"><path d="M0 0H206V40L103 58 0 40z" fill="var(--charcoal)"/></svg>
  <div class="consult-text">
    <div class="lead">Contact Us Now And Get Your</div>
    <div class="big">FREE CONSULTATION</div>
    <div class="today">— Today —</div>
  </div>
  <h5>WELLNESS BEGINS HERE</h5>
  <div class="field" style="top:87px">First Name</div>
  <div class="field" style="top:110px">Last Name</div>
  <div class="field" style="top:134px">Phone Number</div>
  <div class="field" style="top:157px;height:32px;padding-top:12px">Comment....</div>
  <div class="submit">SUBMIT</div>
</aside>

<aside class="hours abs">
  <h3>OFFICE HOURS</h3>
  <table>
    <tr><td class="day">Monday</td><td>: 8:00-11:00, &nbsp;&nbsp;2:00-5:00</td></tr>
    <tr><td class="day">Tuesday</td><td>: 8:30-11:00, &nbsp;&nbsp;2:00-5:30</td></tr>
    <tr><td class="day">Wednesday</td><td>: 8:00-11:00, &nbsp;&nbsp;2:00-5:00</td></tr>
    <tr><td class="day">Thursday</td><td>: 10:00-12:00, &nbsp;2:30-5:00</td></tr>
    <tr><td class="day">Friday</td><td>: 8:00-10:00, &nbsp;&nbsp;1:00-5:00</td></tr>
    <tr><td class="day">Saturday</td><td>: Closed</td></tr>
    <tr><td class="day">Sunday</td><td>: Closed</td></tr>
  </table>
</aside>

<footer class="site-footer abs">
  <div class="tab tab-info abs cond">BASIC INFORMATION</div>
  <div class="tab tab-news abs cond">NEWS LATTERS</div>

  <div class="footer-contact abs">
    <div class="footer-heading">CONTACT</div>
    <div class="row">
      <svg width="16" height="24" viewBox="0 0 16 24"><path d="M8 0A8 8 0 0 0 0 8c0 6 8 16 8 16s8-10 8-16a8 8 0 0 0-8-8z" fill="#fff"/><circle cx="8" cy="8" r="3" fill="#111"/></svg>
      <span>3168 PELHAM ORCHARD LANE, #240<br>BROOKHAVEN, MN 55390</span>
    </div>
    <div class="row">
      <svg width="19" height="19" viewBox="0 0 19 19"><circle cx="9.5" cy="9.5" r="8.5" fill="none" stroke="#fff" stroke-width="1.5"/><path d="M6 5c.6 3.5 2.8 6.6 7 8l1-1.5-1.8-1.1-.9.9c-1.5-.7-2.7-2-3.3-3.7l.9-.9L7.8 5z" fill="#fff"/></svg>
      <span>555-314-2719</span>
    </div>
    <div class="row">
      <svg width="19" height="15" viewBox="0 0 19 15"><rect x="1" y="1" width="17" height="13" fill="none" stroke="#fff" stroke-width="1.4"/><path d="M1 1l8.5 7L18 1" fill="none" stroke="#fff" stroke-width="1.4"/></svg>
      <span>hello@evergreenpath.example</span>
    </div>
  </div>

  <div class="map abs" role="img" aria-label="Street map of the clinic's surroundings with a red location marker"></div>

  <div class="footer-hours abs">
    <div class="footer-heading">OFFICE HOURS</div>
    <ul>
      <li><b>MONDAY:</b>8:00-11:00, &nbsp;2:00-5:00</li>
      <li><b>TUESDAY:</b>8:30-11:00, &nbsp;2:00-5:30</li>
      <li><b>WEDNESDAY:</b>8:00-11:00, &nbsp;2:00-5:00</li>
      <li><b>THURSDAY :</b>10:00-12:00, &nbsp;2:30-5:00</li>
      <li><b>FRIDAY:</b>8:00-10:00, &nbsp;1:00-5:00</li>
      <li><b>SATURDAY:</b>CLOSED</li>
      <li><b>SUNDAY:</b>CLOSED</li>
    </ul>
  </div>
</footer>

</body>
</html>
```